Business card design for new eCommerce site focusing on integrity and strong businsess tactics

We need a business card that will stand out and be memorable. Something with color that matches our company logo colors. Think high end version of Pactivo. There are 2 logos provided. The parent company is called Amber Ledge Partners and we are presenting a new and very exciting eCommerce site called BrightHarborTrade.example.

Target Market(s)

Our target markets are in the Activities, Food and Beverage, Health and Beauty

Industry/Entity Type

Marketing

Contact Information for Business Card

We have 4 members that need cards...I will provide all info to the winner of the design contest
Business Address is
4870 West 63rd Avenue, Suite C207
Phoenix AZ 85731

Font styles to use
Serif
Sans Serif

Colors

Designer to choose colors to be used in the design.

Requirements
Must have
• The card must be memorable...should be unique in design but must exude integrity and be playful .
• I have provided several colors or our parent company...please feel free to use which ever
Nice to have
• I will leave this up to you. Feel free to use other images of your choosing that wraps around our client.....Activities, Dining, Health, Beauty
Should not have
• just dont be boring

```html
<!DOCTYPE html>
<html lang="en">
<head>
<meta charset="utf-8">
<title>BrightHarborTrade.example — Business Card</title>
<link rel="stylesheet" href="https://fonts.googleapis.com/css2?family=Open+Sans:wght@400;500;600;700&display=swap">
<style>
  :root {
    --backdrop: #2a2a2a;
    --brand-blue: #2b77a8;
    --brand-green: #8cc63f;
    --paper: #f4f4f4;
    --ink: #555a5e;
  }
  * { margin: 0; padding: 0; box-sizing: border-box; }
  html, body { width: 1200px; height: 960px; overflow: hidden; }
  body {
    background: var(--backdrop);
    font-family: "Open Sans", Arial, sans-serif;
    position: relative;
  }
  .card {
    position: absolute;
    width: 600px;
    height: 342px;
    overflow: hidden;
  }
  .card--front { left: 314px; top: 113px; background: var(--paper); }
  .card--back { left: 311px; top: 472px; background: var(--brand-blue); }

  .front-band { position: absolute; left: 0; top: 0; }

  .brand-block {
    position: absolute;
    right: 40px;
    top: 58px;
    text-align: right;
  }
  .brand-name {
    font-size: 22px;
    font-weight: 600;
    color: var(--brand-green);
    line-height: 1;
    letter-spacing: -0.3px;
    white-space: nowrap;
  }
  .brand-tagline {
    margin-top: 6px;
    font-size: 10.5px;
    letter-spacing: 1px;
    color: var(--ink);
    white-space: nowrap;
  }

  .holder {
    position: absolute;
    right: 40px;
    top: 135px;
    text-align: right;
  }
  .holder-name {
    font-size: 20px;
    font-weight: 500;
    color: var(--brand-blue);
    line-height: 1.1;
  }
  .holder-role {
    font-size: 14px;
    color: var(--brand-green);
    line-height: 1.3;
  }

  .address {
    position: absolute;
    right: 40px;
    top: 187px;
    text-align: right;
    font-size: 13.5px;
    font-style: normal;
    line-height: 19px;
    color: var(--ink);
    white-space: nowrap;
  }

  .contacts {
    position: absolute;
    right: 40px;
    top: 232px;
    list-style: none;
    font-size: 13.5px;
    line-height: 19px;
    color: var(--ink);
    white-space: nowrap;
  }
  .contacts li {
    display: flex;
    justify-content: flex-end;
    align-items: center;
    gap: 6px;
  }
  .contact-icon { width: 13px; height: 13px; flex: none; }

  .back-mark {
    position: absolute;
    left: 50%;
    top: 70px;
    transform: translateX(-50%);
  }
  .back-name {
    position: absolute;
    left: 0;
    right: 0;
    top: 224px;
    text-align: center;
    font-size: 30px;
    font-weight: 700;
    color: var(--brand-green);
    line-height: 1;
    white-space: nowrap;
  }
</style>
</head>
<body>

<section class="card card--front" aria-label="Business card front">
  <svg class="front-band" width="600" height="342" viewBox="0 0 600 342" aria-hidden="true">
    <path d="M0,0 L98,0 C80,120 150,262 305,342 L0,342 Z" fill="var(--brand-blue)"/>
  </svg>

  <div class="brand-block">
    <div class="brand-name">BrightHarborTrade.example</div>
    <div class="brand-tagline">Trusted Local Deals, Every Day</div>
  </div>

  <div class="holder">
    <div class="holder-name">DANIEL REYES</div>
    <div class="holder-role">CEO/FOUNDER</div>
  </div>

  <address class="address">
    4870 West 63rd Avenue<br>
    Suite C207, Phoenix AZ 85731
  </address>

  <ul class="contacts">
    <li>602 418 7731
      <svg class="contact-icon" viewBox="0 0 16 16" aria-hidden="true"><path d="M3.5 1.5l2.5 0 1.2 3.3-1.7 1.2c.8 1.8 2.2 3.2 4 4l1.2-1.7 3.3 1.2v2.5c0 .8-.7 1.5-1.5 1.5C6.6 13.5 2 8.9 2 3c0-.8.7-1.5 1.5-1.5z" fill="var(--brand-blue)"/></svg>
    </li>
    <li>480 925 3164
      <svg class="contact-icon" viewBox="0 0 16 16" aria-hidden="true"><rect x="4" y="1" width="8" height="14" rx="1.5" fill="none" stroke="var(--brand-blue)" stroke-width="1.6"/><circle cx="8" cy="12.5" r=".9" fill="var(--brand-blue)"/></svg>
    </li>
    <li>daniel@brightharbortrade.example
      <svg class="contact-icon" viewBox="0 0 16 16" aria-hidden="true"><rect x="1" y="3.5" width="14" height="9" fill="var(--brand-blue)"/><path d="M1.5 4l6.5 5 6.5-5" fill="none" stroke="#fff" stroke-width="1.1"/></svg>
    </li>
    <li>www.brightharbortrade.example
      <svg class="contact-icon" viewBox="0 0 16 16" aria-hidden="true"><circle cx="8" cy="8" r="6.5" fill="var(--brand-blue)"/><path d="M1.5 8h13M8 1.5c-2.2 2.2-2.2 10.8 0 13M8 1.5c2.2 2.2 2.2 10.8 0 13" fill="none" stroke="#fff" stroke-width=".9"/></svg>
    </li>
  </ul>
</section>

<section class="card card--back" aria-label="Business card back">
  <svg class="back-mark" width="146" height="146" viewBox="0 0 146 146" aria-hidden="true">
    <circle cx="73" cy="73" r="71" fill="var(--brand-green)"/>
  </svg>
  <div class="back-name">Amber Ledge Partners</div>
</section>

</body>
</html>
```